KRL Stationery Design Project

Dear Designers,
We need a new stationery design for company to match our new logo.
Designers should provide a design for the following:
1. Business Card: 3.5x2 Inches.
2. Letterhead: A4 size.
3. Envelops: 25x35.5 Cm.
You can keep the Arabic name at the bottom of the logo Or you can use the separate attached Arabic Name.
Please refer to the attached logo guide for design information.
Sample Business Card information:
Name: Tarek Sowan
Position: Operation Manager
Tel: +966 920007164 Ex. 500
Fax: +966 (3)8842617
Mob: +966 (5)00263817
email: tarek@krl-example.com.sa
URL: www.krl-example.com.sa
Address:
Nakheel Heights, Suite 718
Zayed bin Omar Str.
Khobar, 31847
Saudi Arabia
Updates
Dear All,
Please note, we had uploaded our logo along with Arabic writing in Adobe illustrator format (.ai).
Regards,
Karim
Dear All,
A sample data for the business card had been added as per your request.
Regards,
Karim

```html
<!DOCTYPE html>
<html lang="en">
<head>
<meta charset="utf-8">
<title>KRL Envelope</title>
<link href="https://fonts.googleapis.com/css2?family=Ubuntu:wght@400;700&display=swap" rel="stylesheet">
<style>
  :root {
    --page-bg: #e4e4e6;
    --paper: #ffffff;
    --navy: #1c3b6c;
    --frame-grey: #c9c9cb;
  }
  html, body {
    margin: 0;
    padding: 0;
    width: 1200px;
    height: 787px;
    overflow: hidden;
    background: var(--page-bg);
    font-family: "Ubuntu", sans-serif;
  }
  .envelope {
    position: absolute;
    left: 137px;
    top: 67px;
    width: 926px;
    height: 653px;
    background: var(--paper);
    box-shadow: 0 2px 10px rgba(0,0,0,0.12);
  }
  .envelope-frame {
    position: absolute;
    left: 0;
    top: 0;
    width: 926px;
    height: 653px;
  }
  .brand {
    position: absolute;
    left: 66px;
    top: 100px;
    display: flex;
    align-items: center;
    gap: 12px;
  }
  .brand-mark {
    width: 22px;
    height: 22px;
    background: var(--navy);
  }
  .brand-name {
    font-weight: 700;
    font-size: 50px;
    line-height: 1;
    color: var(--navy);
    letter-spacing: 1px;
  }
  .sender-details {
    position: absolute;
    left: 66px;
    top: 540px;
    margin: 0;
    font-size: 13px;
    line-height: 20.5px;
    color: var(--navy);
  }
  .sender-details span { display: block; }
</style>
</head>
<body>
  <main class="envelope">
    <svg class="envelope-frame" viewBox="0 0 926 653" aria-hidden="true">
      <rect x="29" y="46" width="871" height="584" rx="36" ry="36"
            fill="none" stroke="var(--frame-grey)" stroke-width="5"/>
    </svg>

    <div class="brand">
      <div class="brand-mark"></div>
      <div class="brand-name">KRL</div>
    </div>

    <address class="sender-details" style="font-style: normal;">
      <span>Nakheel Heights, Suite 718, Zayed bin Omar Str., Khobar, 31847, Saudi Arabia</span>
      <span>Tel: +966 920007164 Ex. 500 | Fax: +966 (3)8842617</span>
      <span>email: tarek@krl-example.com.sa | URL: www.krl-example.com.sa</span>
    </address>
  </main>
</body>
</html>
```